Valdo Capital

We need a corporate style website design for a new company based in Shenzhen's Qianhai Special Economic Development Zone, China. We provide a range of financial services to large international investment companies. Typically these companies invest over 5 million RMB. The company is part of a group that consists of NorthKilns, ValdoTrusts and ValdoEquity. Our location and gateway into Qianhai Special Economic Zone is our core advantage. We would like to see designs that Do Not use purple and orange. The website design should be similar to other websites in this family but different enough to give it a unique style (See attached website links for reference). The final design should communicate financial safety and growth. This website will act partly as a business chamber with connections to the government so we would like it to be diplomatic in style.

www.northkilns.example
www.valdotrusts.example

*Nevegation Bar
Should including Homepage, Financial Product, Team, News.
Could refer to www.valdotrusts.example

*Contact Details

Miss Lan
Address:E 728, North Block, KMO Centre, East Sector, Shenzhen Bright Science Campus
Telephone: +86 0755 63920417
Cellphone: +86 13957280316

* Social Media
Should be grouped like:
1. Weibo QRcode+ Weibo
2. Facebook, Twitter, Linkedin.

Industry/Entity Type

Investment

```html
<!DOCTYPE html>
<html lang="en">
<head>
<meta charset="utf-8">
<title>Valdo Capital</title>
<link rel="stylesheet" href="https://fonts.googleapis.com/css2?family=Open+Sans:wght@300;400;600;700&display=swap">
<style>
:root{
  --accent:#1cb6e6;
  --accent-dark:#1395c2;
  --ink:#2b2b2b;
  --text:#555555;
  --muted:#8a8a8a;
  --rule:#e4e4e4;
  --band:#f6f4f4;
  --footer:#333333;
  --footer-bar:#222222;
  --white:#ffffff;
}
*{box-sizing:border-box;margin:0;padding:0}
html,body{width:1200px;height:2244px;overflow:hidden}
body{position:relative;background:var(--white);font-family:"Open Sans",Arial,sans-serif;color:var(--text)}
.abs{position:absolute}
.topline{left:0;top:0;width:1200px;height:4px;background:var(--accent)}

/* header */
.brand{display:flex;align-items:center;gap:14px}
.brand-square{width:44px;height:44px;background:var(--accent)}
.brand-name{font-size:30px;font-weight:400;color:var(--ink);letter-spacing:.2px}
.lang{left:998px;top:19px;width:92px;height:27px;background:#f0f0f0;border-radius:3px;font-size:13px;color:#333;line-height:27px;padding-left:8px}
.lang-flag{position:absolute;left:58px;top:9px;width:16px;height:10px;background:#8aa2c8}
.lang-caret{position:absolute;left:79px;top:12px;border:4px solid transparent;border-top-color:#777}
.phone{left:850px;top:60px;display:flex;align-items:center;gap:12px;font-size:25px;color:#333;font-weight:400}
.nav{left:440px;top:128px;display:flex;gap:0;font-size:14.5px;color:#333}
.nav a{color:inherit;text-decoration:none;padding:0 17px;height:32px;position:relative}
.nav a.active{color:var(--accent)}
.nav a.active::after{content:"";position:absolute;left:12px;right:12px;bottom:0;height:3px;background:var(--accent)}
.header-shadow{left:0;top:159px;width:1200px;height:2px;background:#ddd}

/* hero */
.hero{left:0;top:161px;width:1200px;height:525px;background:linear-gradient(100deg,#7d858c 0%,#b9c2c9 30%,#d9dde0 52%,#9aa6b0 75%,#6d737a 100%)}
.hero-box{left:111px;top:290px;width:427px;height:211px;background:rgba(30,30,30,.82);padding:18px 12px 0 11px}
.hero-title{font-size:27px;font-weight:400;color:var(--white);letter-spacing:.2px}
.hero-title b{font-weight:700}
.hero-text{margin-top:8px;font-size:13.5px;line-height:20px;color:#eee}
.btn{display:inline-block;background:var(--accent);color:var(--white);font-size:13.5px;font-weight:600;text-align:center;border-bottom:3px solid var(--accent-dark)}
.hero-btn{left:124px;top:448px;width:109px;height:37px;line-height:35px}

/* services */
.section-title{font-size:25px;font-weight:400;color:var(--accent)}
.services-rule{left:110px;top:775px;width:982px;height:4px;border-top:1px solid var(--rule);border-bottom:1px solid var(--rule)}
.service{width:270px}
.service-head{display:flex;align-items:flex-end;gap:20px;height:45px}
.service-name{font-size:18px;color:var(--ink);line-height:24px}
.service-name.hl{color:var(--accent)}
.service-text{margin-top:12px;font-size:13.3px;line-height:18px;color:#555}

/* gallery */
.gallery-band{left:0;top:993px;width:1200px;height:507px;background:var(--band)}
.tile{border-radius:4px}
.zoom-ring{left:0;top:0}

/* about & blog */
.rule{height:1px;background:var(--rule)}
.about-text{font-size:13.5px;line-height:19.5px;color:#555}
.about-btn{left:132px;top:1839px;width:112px;height:36px;line-height:34px}
.date{width:48px;height:57px;text-align:center}
.date-day{height:36px;background:#333;color:var(--white);font-size:24px;line-height:36px}
.date-mon{height:21px;background:var(--accent);color:var(--white);font-size:13px;line-height:21px}
.post-name{font-size:14px;color:#333;font-weight:600}
.post-text{margin-top:6px;font-size:13px;line-height:18px;color:#666;width:320px}
.post-more{margin-top:8px;font-size:12.5px;color:var(--accent);text-decoration:underline}
.post-close{width:10px;height:10px;background:#ddd}

/* footer */
.footer{left:0;top:1930px;width:1200px;height:274px;background:var(--footer)}
.footer-bar{left:0;top:2204px;width:1200px;height:40px;background:var(--footer-bar);color:#ddd;font-size:12px;text-align:center;line-height:40px}
.footer .brand-square{width:36px;height:36px;background:var(--white)}
.footer .brand-name{color:var(--white);font-size:25px}
.footer-title{font-size:24px;color:var(--white);font-weight:400}
.footer-text{font-size:13px;line-height:19.5px;color:#ddd}
.tweet-date{display:flex;align-items:center;gap:10px;font-size:14px;font-weight:700;color:#ddd}
.tweet-dot{width:18px;height:18px;border-radius:50%;background:var(--accent)}
.contact-row{display:flex;gap:22px;font-size:13px;line-height:19.5px;color:#ddd}
.contact-row svg{flex:none}
</style>
</head>
<body>
<div class="abs topline"></div>

<header>
  <div class="abs brand" style="left:110px;top:50px">
    <span class="brand-square"></span>
    <span class="brand-name">Valdo Capital</span>
  </div>
  <div class="abs lang">English<span class="lang-flag"></span><span class="lang-caret"></span></div>
  <div class="abs phone">
    <svg width="26" height="26" viewBox="0 0 24 24"><path fill="#1cb6e6" d="M6.6 10.8a15 15 0 0 0 6.6 6.6l2.2-2.2a1 1 0 0 1 1-.25 11.4 11.4 0 0 0 3.6.57 1 1 0 0 1 1 1V20a1 1 0 0 1-1 1A17 17 0 0 1 3 4a1 1 0 0 1 1-1h3.5a1 1 0 0 1 1 1c0 1.25.2 2.45.57 3.57a1 1 0 0 1-.25 1z"/></svg>
    <span>+86 13957280316</span>
  </div>
  <nav class="abs nav">
    <a class="active">Home</a><a>About Us</a><a>Investment Fields</a><a>Partners</a><a>News/Info</a><a>Join Us</a><a>Contact Us</a>
  </nav>
  <div class="abs header-shadow"></div>
</header>

<section>
  <div class="abs hero" role="img" aria-label="Photo of business people smiling around a meeting table"></div>
  <div class="abs hero-box">
    <h1 class="hero-title">WELCOME TO <b>VALDO CAPITAL</b></h1>
    <p class="hero-text">Lorem ipsum dolor sit amet, consectetur adipisicing elit, sed eiusmod tempor incididunt.Ut enim ad minim veniam, quis nostrud exercitation ullamco laboris nisi ut aliquip ex ea commodo consequat.</p>
  </div>
  <a class="abs btn hero-btn">Read More</a>
</section>

<section>
  <h2 class="abs section-title" style="left:110px;top:726px">Our Services</h2>
  <div class="abs services-rule"></div>

  <div class="abs service" style="left:130px;top:815px">
    <div class="service-head">
      <svg width="46" height="44" viewBox="0 0 46 44"><g fill="#333"><rect x="2" y="28" width="6" height="16"/><rect x="11" y="22" width="6" height="22"/><rect x="20" y="25" width="6" height="19"/><rect x="29" y="16" width="6" height="28"/><rect x="38" y="10" width="6" height="34"/><path d="M4 24 L16 14 L24 20 L40 4" stroke="#333" stroke-width="3" fill="none"/><path d="M34 2 L44 2 L44 12 Z"/></g><text x="7" y="14" font-family="Open Sans, sans-serif" font-size="14" font-weight="700" fill="#333">$</text></svg>
      <span class="service-name">Finance</span>
    </div>
    <p class="service-text">Lorem ipsum dolor sit amet, consectetur adipisicing sed eiusmod tempor incididunt Ut enim minim veniam, quis nostrud aute exercitation ullamco.</p>
  </div>

  <div class="abs service" style="left:470px;top:815px">
    <div class="service-head" style="align-items:center">
      <svg width="60" height="36" viewBox="0 0 60 36"><g fill="#1cb6e6"><circle cx="12" cy="10" r="6"/><circle cx="48" cy="10" r="6"/><circle cx="30" cy="8" r="8"/><path d="M0 32c0-8 5-13 12-13s10 4 10 4v9z"/><path d="M60 32c0-8-5-13-12-13s-10 4-10 4v9z"/><path d="M16 36c0-11 6-17 14-17s14 6 14 17z"/></g></svg>
      <span class="service-name hl">Consultancy</span>
    </div>
    <p class="service-text" style="margin-top:9px">Lorem ipsum dolor sit amet, consectetur adipisicing sed eiusmod tempor incididunt Ut enim minim veniam, quis nostrud aute exercitation ullamco.</p>
  </div>

  <div class="abs service" style="left:811px;top:815px">
    <div class="service-head">
      <svg width="56" height="44" viewBox="0 0 56 44"><g fill="#333"><path d="M2 20 L28 2 L54 20 Z"/><rect x="6" y="20" width="44" height="24"/><rect x="38" y="4" width="6" height="10"/></g><g fill="#fff"><rect x="12" y="25" width="8" height="7"/><rect x="36" y="25" width="8" height="7"/><rect x="24" y="30" width="8" height="14"/></g></svg>
      <span class="service-name">Property Management</span>
    </div>
    <p class="service-text">Lorem ipsum dolor sit amet, consectetur adipisicing sed eiusmod tempor incididunt Ut enim minim veniam, quis nostrud aute exercitation ullamco.</p>
  </div>
</section>

<section>
  <div class="abs gallery-band"></div>
  <div class="abs tile" style="left:124px;top:1031px;width:313px;height:209px;background:linear-gradient(180deg,#d5dde3,#3b3d42)" role="img" aria-label="Photo of a young business team in dark suits"></div>
  <div class="abs tile" style="left:444px;top:1031px;width:313px;height:209px;background:linear-gradient(180deg,#a8b2bb,#2f3338)" role="img" aria-label="Photo of businessmen shaking hands outdoors"></div>
  <div class="abs tile" style="left:763px;top:1031px;width:314px;height:209px;background:linear-gradient(180deg,#a59c92,#8f9fb0)" role="img" aria-label="Photo of a businessman on a city street"></div>
  <div class="abs tile" style="left:124px;top:1246px;width:313px;height:208px;background:linear-gradient(160deg,#f2c640,#b56a12 60%,#4a2a08)" role="img" aria-label="Photo of glowing yellow paper lanterns"></div>
  <div class="abs tile" style="left:444px;top:1246px;width:313px;height:208px;background:#2f2e2f" role="img" aria-label="Darkened photo of a woman in a headscarf with a zoom overlay"></div>
  <svg class="abs" style="left:567px;top:1326px" width="52" height="52" viewBox="0 0 52 52"><circle cx="26" cy="26" r="24" fill="none" stroke="#fff" stroke-width="2"/><circle cx="24" cy="24" r="7" fill="none" stroke="#fff" stroke-width="2"/><path d="M29 29 L34 34" stroke="#fff" stroke-width="2.5"/><path d="M21 24h6M24 21v6" stroke="#fff" stroke-width="1.6"/></svg>
  <div class="abs tile" style="left:763px;top:1246px;width:314px;height:208px;background:linear-gradient(150deg,#c9c7cc,#9da0ab 55%,#b8b4b9)" role="img" aria-label="Photo of a terracotta warrior statue"></div>
</section>

<section>
  <h2 class="abs section-title" style="left:132px;top:1562px">About Us</h2>
  <div class="abs rule" style="left:132px;top:1605px;width:462px"></div>
  <p class="abs about-text" style="left:132px;top:1618px;width:470px">Lorem ipsum dolor sit amet, consectetur adipisicing elit, sed do eiusmod tempor incididunt ut labore et dolore magna aliqua. Ut enim ad minim veniam, quis nostrud exercitation ullamco laboris nisi ut aliquip ex ea commodo consequat. Duis aute irure dolor in reprehenderit in voluptate velit esse cillum dolore eu fugiat nulla pariatur. Excepteur sint occaecat cupidatat non proident, sunt in culpa qui officia.</p>
  <p class="abs about-text" style="left:132px;top:1751px;width:470px">Lorem ipsum dolor sit amet, consectetur adipisicing elit, sed do eiusmod tempor incididunt ut labore et dolore magna aliqua.</p>
  <a class="abs btn about-btn">Read More</a>

  <h2 class="abs section-title" style="left:694px;top:1564px">Blog</h2>
  <div class="abs rule" style="left:694px;top:1605px;width:398px"></div>

  <div class="abs date" style="left:697px;top:1634px"><div class="date-day">15</div><div class="date-mon">Dec</div></div>
  <div class="abs" style="left:761px;top:1630px">
    <div class="post-name">Corwin Ashdale</div>
    <p class="post-text">Lorem ipsum dolor sit amet, consec dipiscing elit, sed diam nonummy nibh euismodunt ut laoreet dolore....</p>
    <div class="post-more">Read More</div>
  </div>
  <div class="abs post-close" style="left:1070px;top:1616px"></div>
  <div class="abs rule" style="left:694px;top:1749px;width:292px"></div>

  <div class="abs date" style="left:697px;top:1781px"><div class="date-day">25</div><div class="date-mon">Nov</div></div>
  <div class="abs" style="left:761px;top:1777px">
    <div class="post-name">Corwin Ashdale</div>
    <p class="post-text">Lorem ipsum dolor sit amet, consec dipiscing elit, sed diam nonummy nibh euismodunt ut laoreet dolore....</p>
    <div class="post-more">Read More</div>
  </div>
  <div class="abs post-close" style="left:1070px;top:1763px"></div>
</section>

<footer>
  <div class="abs footer"></div>
  <div class="abs brand" style="left:110px;top:1968px">
    <span class="brand-square"></span>
    <span class="brand-name">Valdo Capital</span>
  </div>
  <p class="abs footer-text" style="left:110px;top:2043px;width:330px">Lorem ipsum dolor sit amet, consectetur adipisicing elit, sed do eiusmod tempor incididunt ut labore et dolore magna aliqua. Ut enim ad minim veniam, quis nostrud exercitation ullamco laboris nisi ut aliquip ex ea commodo consequat.</p>

  <h3 class="abs footer-title" style="left:503px;top:1962px">Latest tweets</h3>
  <p class="abs footer-text" style="left:503px;top:2021px;width:320px">Lorem ipsum dolor sit amet, consectetur adipisicing elit, sed do eiusmod tempor incididunt ut labore et dolore magna aliqua. Ut enim ad minim veniam, quis nostrud exercitation ullamco laboris nisi ut aliquip commodo consequat.</p>
  <div class="abs tweet-date" style="left:505px;top:2137px"><span class="tweet-dot"></span>2 Feb</div>

  <h3 class="abs footer-title" style="left:888px;top:1962px">Contact us</h3>
  <div class="abs contact-row" style="left:888px;top:2021px;width:200px">
    <svg width="16" height="22" viewBox="0 0 16 22"><path fill="#fff" d="M8 0a8 8 0 0 0-8 8c0 6 8 14 8 14s8-8 8-14a8 8 0 0 0-8-8zm0 11a3 3 0 1 1 0-6 3 3 0 0 1 0 6z"/></svg>
    <span>Enter your address here</span>
  </div>
  <div class="abs contact-row" style="left:888px;top:2077px">
    <svg width="18" height="20" viewBox="0 0 24 24"><path fill="#fff" d="M6.6 10.8a15 15 0 0 0 6.6 6.6l2.2-2.2a1 1 0 0 1 1-.25 11.4 11.4 0 0 0 3.6.57 1 1 0 0 1 1 1V20a1 1 0 0 1-1 1A17 17 0 0 1 3 4a1 1 0 0 1 1-1h3.5a1 1 0 0 1 1 1c0 1.25.2 2.45.57 3.57a1 1 0 0 1-.25 1z"/></svg>
    <span>Phone: +86 0755 63920417</span>
  </div>
  <div class="abs contact-row" style="left:886px;top:2122px">
    <svg width="22" height="20" viewBox="0 0 22 20"><g fill="#fff"><rect x="5" y="0" width="10" height="7"/><rect x="0" y="8" width="22" height="12" rx="1"/></g><rect x="4" y="12" width="8" height="2" fill="#333"/></svg>
    <span>Fax: (800) 555-0142</span>
  </div>

  <div class="abs footer-bar">Copyright © 2014 Valdo Capital.. All Rights Reserved.</div>
</footer>
</body>
</html>
```